Fast Growing Personal Injury Law Firm Needs Business Card Design

We need a business card design for a fast growing personal injury law firm in Florida. Our name is Dorian Kalvenfeld, P.A. Our practice is comprised of younger attorneys (in their 30s) that employ more modern techniques/tools than our older competition. We would prefer a look that is a modern play on a classic look. Also, we would like to continue using a color scheme that employs navy blue and kelly green (other shades of green could be fine too) as well as our "E" logo.

Industry/Entity Type

Law Firm

```html
<!DOCTYPE html>
<html lang="en">
<head>
<meta charset="utf-8">
<title>Dorian Kalvenfeld, P.A. — Business Card</title>
<link href="https://fonts.googleapis.com/css2?family=Cinzel:wght@500&family=Lato:wght@400&display=swap" rel="stylesheet">
<style>
  :root {
    --navy: #10295e;
    --green: #13813f;
    --ink: #333333;
    --paper: #ffffff;
    --backdrop: #4a4a4a;
    --rule: #d6d6d6;
  }
  * { margin: 0; padding: 0; box-sizing: border-box; }
  html, body { width: 1200px; height: 820px; overflow: hidden; }
  body { background: var(--backdrop); position: relative; font-family: "Lato", sans-serif; }

  .card { position: absolute; background: var(--paper); width: 477px; height: 275px; overflow: hidden; }
  .card--front { left: 115px; top: 257px; }
  .card--back { left: 621px; top: 257px; border-top: 2px solid var(--navy); }

  /* front */
  .brand-block { position: absolute; left: 55px; top: 80px; width: 141px; text-align: center; }
  .brand-block__square { width: 44px; height: 44px; background: var(--navy); margin: 0 auto 12px; }
  .brand-block__name { font-family: "Cinzel", serif; font-weight: 500; font-size: 15px; color: var(--navy); line-height: 1.25; }

  .divider { position: absolute; left: 239px; top: 50px; width: 1px; height: 182px;
    background: linear-gradient(to bottom, transparent, var(--rule) 20%, var(--rule) 80%, transparent); }

  .contact { position: absolute; left: 272px; top: 40px; color: var(--ink); }
  .contact__name { font-size: 17px; color: var(--navy); line-height: 22px; }
  .contact__title { font-size: 13px; line-height: 18px; color: #222; }
  .contact__address { font-size: 13px; line-height: 16px; margin-top: 19px; }
  .contact__list { list-style: none; margin-top: 13px; font-size: 12.5px; }
  .contact__list li { display: flex; align-items: center; height: 19.5px; }
  .contact__list svg { width: 11px; height: 11px; margin-right: 5px; flex: none; }

  .card__bands { position: absolute; left: 0; bottom: 0; width: 477px; height: 21px; }

  /* back */
  .wordmark { position: absolute; left: 62px; top: 111px; display: flex; align-items: center; }
  .wordmark__square { width: 72px; height: 62px; background: var(--navy); margin-right: 12px; flex: none; }
  .wordmark__name { font-family: "Cinzel", serif; font-weight: 500; font-size: 21px; color: var(--navy);
    line-height: 26px; padding-bottom: 5px; border-bottom: 1px solid var(--navy); white-space: nowrap; }
  .wordmark__tagline { font-family: "Cinzel", serif; font-weight: 500; font-size: 13.5px; color: var(--green);
    letter-spacing: 1.6px; margin-top: 4px; white-space: nowrap; }
</style>
</head>
<body>

<section class="card card--front" aria-label="Business card front">
  <div class="brand-block">
    <div class="brand-block__square"></div>
    <div class="brand-block__name">Dorian Kalvenfeld, P.A.</div>
  </div>

  <div class="divider"></div>

  <div class="contact">
    <p class="contact__name">Dorian Kalvenfeld</p>
    <p class="contact__title">Attorney at Law</p>
    <p class="contact__address">2315 Harborview Parkway Suite 400<br>Palmetto Shores, Florida 34119</p>
    <ul class="contact__list">
      <li>
        <svg viewBox="0 0 12 12" aria-hidden="true"><circle cx="6" cy="6" r="6" fill="var(--navy)"/><path d="M4 3l1.2 1.4-.6.9c.4.8 1 1.4 1.8 1.8l.9-.6L8.7 8 8 9C5.6 8.8 3.2 6.4 3 4z" fill="#fff"/></svg>
        941.555.0172
      </li>
      <li>
        <svg viewBox="0 0 12 12" aria-hidden="true"><circle cx="6" cy="6" r="6" fill="var(--navy)"/><rect x="4" y="2.6" width="4" height="6.8" rx=".7" fill="#fff"/><rect x="4.7" y="3.5" width="2.6" height="4.2" fill="var(--navy)"/></svg>
        941.555.0148
      </li>
      <li>
        <svg viewBox="0 0 12 12" aria-hidden="true"><circle cx="6" cy="6" r="6" fill="var(--navy)"/><rect x="3" y="4" width="6" height="4.2" fill="#fff"/><path d="M3 4l3 2.4L9 4" fill="none" stroke="var(--navy)" stroke-width=".7"/></svg>
        dorian@kalvenfeldlaw.com
      </li>
      <li>
        <svg viewBox="0 0 12 12" aria-hidden="true"><circle cx="6" cy="6" r="6" fill="var(--navy)"/><circle cx="6" cy="6" r="3.3" fill="none" stroke="#fff" stroke-width=".8"/><path d="M2.7 6h6.6M6 2.7c-1.4 1.8-1.4 4.8 0 6.6M6 2.7c1.4 1.8 1.4 4.8 0 6.6" fill="none" stroke="#fff" stroke-width=".6"/></svg>
        www.kalvenfeldlaw.com
      </li>
    </ul>
  </div>

  <svg class="card__bands" viewBox="0 0 477 21" aria-hidden="true">
    <polygon points="0,2 252,2 243,11 0,11" fill="var(--green)"/>
    <polygon points="256,0 477,0 477,21 0,21 0,12 246,12" fill="var(--navy)"/>
  </svg>
</section>

<section class="card card--back" aria-label="Business card back">
  <div class="wordmark">
    <div class="wordmark__square"></div>
    <div>
      <div class="wordmark__name">Dorian Kalvenfeld, P.A.</div>
      <div class="wordmark__tagline">Personal Injury Attorneys</div>
    </div>
  </div>
</section>

</body>
</html>
```